Employee Benefits and Insurance Consulting

We are an existing company with over 30 years experience but are changing our name. We would like a simple design with grey tones.

Industry/Entity Type

Insurance

Contact Information for Business Card

Marlow Benefits Consulting
Gerald P Hollins CEO
5172 Brackenridge Road
Fairbrook, TN 37854
gerald@marlowbenefits-example.com
865-412-5593 - O
865-247-3861 - C

```html
<!DOCTYPE html>
<html lang="en">
<head>
<meta charset="utf-8">
<title>Marlow Benefits Consulting – Business Card</title>
<link rel="stylesheet" href="https://fonts.googleapis.com/css2?family=Tenor+Sans&family=Arimo:wght@400&display=swap">
<style>
  :root {
    --backdrop: #1f5560;
    --card-light: #eef1f2;
    --card-band: #6e7074;
    --card-band-edge: #5d5f63;
    --ink-dark: #55504f;
    --ink-light: #ffffff;
    --ink-soft: #e6e7e8;
  }
  * { box-sizing: border-box; margin: 0; padding: 0; }
  html, body {
    width: 1200px;
    height: 799px;
    overflow: hidden;
    background: var(--backdrop);
  }
  .business-card {
    position: absolute;
    left: 75px;
    top: 100px;
    width: 1050px;
    height: 600px;
    background: var(--card-light);
    box-shadow: 0 10px 30px rgba(0, 0, 0, 0.35);
    overflow: hidden;
  }
  .brand {
    position: absolute;
    top: 120px;
    left: 0;
    width: 100%;
    display: flex;
    align-items: center;
    justify-content: center;
    gap: 18px;
  }
  .brand-dot {
    width: 22px;
    height: 22px;
    border-radius: 50%;
    background: var(--ink-dark);
  }
  .brand-name {
    font-family: "Tenor Sans", sans-serif;
    font-size: 44px;
    color: var(--ink-dark);
    letter-spacing: 0.5px;
  }
  .info-band {
    position: absolute;
    left: 0;
    top: 345px;
    width: 100%;
    height: 255px;
    background: var(--card-band);
    border-top: 14px solid var(--card-band-edge);
  }
  .holder {
    position: absolute;
    left: 70px;
    top: 50px;
    color: var(--ink-light);
    font-family: "Tenor Sans", sans-serif;
  }
  .holder-name {
    font-size: 44px;
    letter-spacing: 0.3px;
  }
  .holder-title {
    font-size: 22px;
    color: var(--ink-soft);
    font-style: italic;
    margin-top: 6px;
    margin-left: 110px;
  }
  .contact {
    position: absolute;
    left: 630px;
    top: 40px;
    font-family: "Arimo", sans-serif;
    font-size: 21px;
    color: var(--ink-light);
    list-style: none;
  }
  .contact-item {
    display: flex;
    align-items: center;
    gap: 12px;
    height: 32px;
  }
  .contact-item svg { width: 22px; height: 22px; flex: none; }
  .address {
    position: absolute;
    left: 664px;
    top: 158px;
    font-family: "Arimo", sans-serif;
    font-size: 19px;
    line-height: 29px;
    color: var(--ink-soft);
    font-style: normal;
  }
</style>
</head>
<body>
  <article class="business-card">
    <header class="brand">
      <span class="brand-dot"></span>
      <span class="brand-name">Marlow Benefits Consulting</span>
    </header>

    <section class="info-band">
      <div class="holder">
        <div class="holder-name">Gerald P Hollins</div>
        <div class="holder-title">(CEO)</div>
      </div>

      <ul class="contact">
        <li class="contact-item">
          <svg viewBox="0 0 22 22" aria-hidden="true">
            <circle cx="11" cy="11" r="10" fill="none" stroke="#fff" stroke-width="1.6"/>
            <rect x="7.5" y="5" width="7" height="12" rx="1.3" fill="none" stroke="#fff" stroke-width="1.5"/>
            <line x1="10" y1="15" x2="12" y2="15" stroke="#fff" stroke-width="1.3"/>
          </svg>
          <span>865-247-3861</span>
        </li>
        <li class="contact-item">
          <svg viewBox="0 0 22 22" aria-hidden="true">
            <circle cx="11" cy="11" r="10.5" fill="#fff"/>
            <path d="M7.5 6 l2 -0.5 l1.3 3 l-1.3 1 q1 2.3 3 3.3 l1 -1.3 l3 1.3 l-0.5 2 q-5.5 0.5 -8.5 -8.8z" fill="#6e7074"/>
          </svg>
          <span>865-412-5593</span>
        </li>
        <li class="contact-item">
          <svg viewBox="0 0 22 22" aria-hidden="true">
            <rect x="2" y="5" width="18" height="12" fill="#fff"/>
            <path d="M2 5 l9 7 l9 -7" fill="none" stroke="#6e7074" stroke-width="1.4"/>
          </svg>
          <span>gerald@marlowbenefits-example.com</span>
        </li>
      </ul>

      <address class="address">
        5172 Brackenridge Road<br>
        Fairbrook, TN 37854
      </address>
    </section>
  </article>
</body>
</html>
```